I would like a standard letter head document that is innovative and not 'typically' corporate.
I would like a BLACK panel of some sort so that the logo can be best showcased within that (as the logo has a black background).
I would like the three words 'dream', 'believe', 'achieve'
inscribed at the side (as per the example I uploaded). Its should be more like a watermark so only just visible.
I would like the K symbol as a water mark on the page (similar to the lion on the example I uploaded).
I would like the following details also included.
Lydia Contwell
Personal Training/Nutrition/Life Coaching
www.plovexa.com.au
0412 574 209

```html
<!DOCTYPE html>
<html lang="en">
<head>
<meta charset="utf-8">
<title>Plovexa Personal Training – Stationery</title>
<link rel="stylesheet" href="https://fonts.googleapis.com/css2?family=Open+Sans:wght@400;700;800&display=swap">
<style>
  :root {
    --ink: #141414;
    --teal: #1aa3a6;
    --paper: #ffffff;
    --backdrop: #d6d6d6;
    --light-text: #ffffff;
    --muted: #2a2a2a;
  }
  * { margin: 0; padding: 0; box-sizing: border-box; }
  html, body { width: 1200px; height: 849px; overflow: hidden; }
  body {
    background: var(--backdrop);
    font-family: "Open Sans", Arial, sans-serif;
    position: relative;
  }
  .sheet {
    position: absolute;
    background: var(--paper);
    box-shadow: 0 0 0 1px rgba(0,0,0,0.08);
    overflow: hidden;
  }
  .sheet svg.bands { position: absolute; inset: 0; width: 100%; height: 100%; }

  .letterhead { left: 134px; top: 53px; width: 467px; height: 660px; }
  .envelope { left: 557px; top: 260px; width: 512px; height: 244px; }

  .brand { position: absolute; display: flex; align-items: center; gap: 8px; }
  .brand-dot { border-radius: 50%; background: var(--teal); flex: none; }
  .brand-name {
    color: var(--teal); font-weight: 800; letter-spacing: 1px; line-height: 1;
  }
  .brand-tag {
    position: absolute; color: var(--light-text); font-weight: 700;
    letter-spacing: 2.5px; line-height: 1;
  }

  .letterhead .brand { left: 26px; top: 30px; }
  .letterhead .brand-dot { width: 16px; height: 16px; }
  .letterhead .brand-name { font-size: 30px; }
  .letterhead .brand-tag { left: 72px; top: 66px; font-size: 12.5px; }

  .envelope .brand { left: 22px; top: 14px; }
  .envelope .brand-dot { width: 10px; height: 10px; }
  .envelope .brand-name { font-size: 19px; }
  .envelope .brand-tag { left: 52px; top: 39px; font-size: 8px; letter-spacing: 1.8px; }

  .contact { position: absolute; line-height: 1.2; }
  .contact .contact-name { font-weight: 800; }
  .contact .contact-line { font-weight: 400; }

  .letterhead .contact { left: 330px; top: 24px; color: var(--muted); }
  .letterhead .contact-name { font-size: 9.5px; color: var(--ink); }
  .letterhead .contact-line { font-size: 5.8px; }

  .envelope .contact { left: 36px; top: 205px; color: var(--light-text); }
  .envelope .contact-name { font-size: 8px; }
  .envelope .contact-line { font-size: 5px; }

  .footer-url {
    position: absolute; left: 48px; top: 646px;
    color: var(--light-text); font-size: 6.5px; font-weight: 700;
  }
</style>
</head>
<body>

  <section class="sheet letterhead" aria-label="Letterhead">
    <svg class="bands" viewBox="0 0 467 660" preserveAspectRatio="none" aria-hidden="true">
      <polygon points="0,0 467,0 467,44 0,128" fill="var(--ink)"/>
      <polygon points="305,0 467,0 467,44 295,75" fill="var(--teal)"/>
      <polygon points="0,595 467,632 467,660 0,660" fill="var(--ink)"/>
      <polygon points="184,610 467,632 467,660 168,660" fill="var(--teal)"/>
    </svg>

    <div class="brand">
      <span class="brand-dot"></span>
      <span class="brand-name">PLOVEXA</span>
    </div>
    <div class="brand-tag">PERSONAL TRAINING</div>

    <div class="contact">
      <p class="contact-name">Lydia Contwell</p>
      <p class="contact-line">Personal Training/Nutrition/Life Coaching</p>
      <p class="contact-line">www.plovexa.com.au</p>
      <p class="contact-line">0412 574 209</p>
    </div>

    <p class="footer-url">www.plovexa.com.au</p>
  </section>

  <section class="sheet envelope" aria-label="Envelope">
    <svg class="bands" viewBox="0 0 512 244" preserveAspectRatio="none" aria-hidden="true">
      <polygon points="0,0 512,0 512,15.5 0,64" fill="var(--ink)"/>
      <polygon points="344,0 512,0 512,15.5 336,32" fill="var(--teal)"/>
      <polygon points="0,190 254,244 0,244" fill="var(--ink)"/>
    </svg>

    <div class="brand">
      <span class="brand-dot"></span>
      <span class="brand-name">PLOVEXA</span>
    </div>
    <div class="brand-tag">PERSONAL TRAINING</div>

    <div class="contact">
      <p class="contact-name">Lydia Contwell</p>
      <p class="contact-line">Personal Training/Nutrition/Life Coaching</p>
      <p class="contact-line">www.plovexa.com.au</p>
      <p class="contact-line">0412 574 209</p>
    </div>
  </section>

</body>
</html>
```